KAJU Freightways #ALLKAJU Business Cards & Letterhead

I am looking to business cards designed for our organization. We are currently undergoing a small re-branding that is taking place. Our organization is called KAJU Freightways and we are headquartered in Phoenix, AZ. We primarily provide transportation and logistics services to the Marlow Parcel Bureau who is our largest customer. I would like to see a design that incorporates name, title, contact info, website, and address (this will be different depending on the employee). I would also like to see some color on the business card using our logo colors or a variation. I would like our logo on the back of the business card with the website displayed. The final design should communicate that we are a next generation transportation operate that focuses on being driver-first, customer-centric, innovative, and sustainable.We would also like our #ALLKAJU catch phrase incorporated as well.

Target Market(s)

Transportation & Logistics

Industry/Entity Type

Trucking Company

Contact Information for Business Card

-First and Last Name
-Position Title
-Contact Phone
-Contact Email
-Physical Address

Font styles to use
Serif

Colors

Designer to choose colors to be used in the design.

Requirements
Must have
• -KAJU logo prominently displayed
• -#ALLKAJU catch phrase used
• -Some amount of color, design gradient, etc.
• -Logo on the back with website listed (https://www.kajufreightco.example)

```html
<!DOCTYPE html>
<html lang="en">
<head>
<meta charset="utf-8">
<title>KAJU Freightways Business Card</title>
<link href="https://fonts.googleapis.com/css2?family=Roboto:wght@400;500;700;900&family=Roboto+Condensed:wght@700&display=swap" rel="stylesheet">
<style>
  :root {
    --bg: #b9b9b9;
    --card: #f3f3f2;
    --navy: #0d3440;
    --green: #6cab26;
    --white: #ffffff;
  }
  * { box-sizing: border-box; margin: 0; padding: 0; }
  html, body { width: 1200px; height: 576px; overflow: hidden; }
  body {
    background: var(--bg);
    font-family: "Roboto", Arial, sans-serif;
    color: var(--navy);
    position: relative;
  }
  .card {
    position: absolute;
    width: 484px;
    height: 293px;
    background: var(--card);
    border-radius: 10px;
    overflow: hidden;
    box-shadow: 0 3px 6px rgba(0,0,0,0.25);
  }
  .card--back { left: 82px; top: 139px; }
  .card--front { left: 602px; top: 138px; }

  .brand-mark {
    position: absolute;
    display: flex;
    align-items: center;
    gap: 10px;
  }
  .brand-dot {
    border-radius: 50%;
    background: var(--green);
    flex: none;
  }
  .brand-name {
    font-family: "Roboto", Arial, sans-serif;
    font-weight: 900;
    color: var(--navy);
    letter-spacing: 1px;
    line-height: 1;
  }
  .card--back .brand-mark { left: 0; right: 0; top: 112px; justify-content: center; }
  .card--back .brand-dot { width: 22px; height: 22px; }
  .card--back .brand-name { font-size: 48px; }
  .card--front .brand-mark { right: 28px; top: 88px; }
  .card--front .brand-dot { width: 22px; height: 22px; }
  .card--front .brand-name { font-size: 50px; }

  .catch-phrase {
    position: absolute;
    left: 0; right: 0; top: 176px;
    text-align: center;
    font-size: 13px;
    font-weight: 700;
    letter-spacing: 2px;
    color: var(--green);
  }

  .website-line {
    position: absolute;
    left: 0; right: 0; top: 250px;
    display: flex;
    align-items: center;
    justify-content: center;
    gap: 20px;
    font-size: 13px;
    letter-spacing: 2.4px;
  }
  .website-line .dash { width: 34px; height: 2px; background: var(--green); border-radius: 1px; }

  .split-band { position: absolute; left: 0; right: 0; bottom: 0; height: 12px; display: flex; }
  .split-band span { flex: 1; }
  .split-band .navy { background: var(--navy); }
  .split-band .green { background: var(--green); }

  .holder { position: absolute; left: 22px; top: 36px; }
  .holder-name {
    font-family: "Roboto Condensed", "Arial Narrow", sans-serif;
    font-weight: 700;
    font-size: 20px;
    color: var(--green);
  }
  .holder-title { font-size: 13px; margin-top: 4px; }

  .address { position: absolute; left: 22px; top: 168px; font-size: 13px; line-height: 18px; font-style: normal; }

  .contacts { position: absolute; left: 22px; top: 214px; list-style: none; font-size: 13px; }
  .contacts li { display: flex; align-items: center; height: 18.5px; }
  .contacts svg { width: 11px; height: 11px; margin: 0 14px 0 6px; fill: var(--green); }

  .front-footer { position: absolute; left: 0; bottom: 0; width: 484px; height: 36px; }
  .company-tag {
    position: absolute;
    right: 22px; bottom: 9px;
    color: var(--white);
    font-size: 12.5px;
  }
</style>
</head>
<body>

<section class="card card--back" aria-label="Card back">
  <div class="brand-mark"><span class="brand-dot"></span><span class="brand-name">KAJU</span></div>
  <p class="catch-phrase">#ALLKAJU</p>
  <p class="website-line"><span class="dash"></span>www.kajufreightco.example<span class="dash"></span></p>
  <div class="split-band"><span class="navy"></span><span class="green"></span></div>
</section>

<section class="card card--front" aria-label="Card front">
  <div class="holder">
    <h1 class="holder-name">Dorian Vell</h1>
    <p class="holder-title">Chairman &amp; CEO</p>
  </div>

  <div class="brand-mark"><span class="brand-dot"></span><span class="brand-name">KAJU</span></div>

  <address class="address">
    4170 North Cinder Ridge<br>Road Phoenix, AZ 85099
  </address>

  <ul class="contacts">
    <li>
      <svg viewBox="0 0 12 12"><path d="M1 4c0-2 2-3 5-3s5 1 5 3v1H8V4H4v1H1zM2 6h8l1 5H1z"/></svg>
      602-555-0148
    </li>
    <li>
      <svg viewBox="0 0 12 12"><path d="M0 2h12v8H0z"/><path d="M0 2l6 5 6-5" fill="none" stroke="#f3f3f2" stroke-width="1.2"/></svg>
      dorian@kajufreightco.example
    </li>
    <li>
      <svg viewBox="0 0 12 12"><circle cx="6" cy="6" r="5.5"/><path d="M0.5 6h11M6 0.5v11M2 3h8M2 9h8" stroke="#f3f3f2" stroke-width="0.8" fill="none"/></svg>
      www.kajufreightco.example
    </li>
  </ul>

  <svg class="front-footer" viewBox="0 0 484 36" aria-hidden="true">
    <rect x="0" y="30" width="280" height="6" fill="var(--green)"/>
    <path d="M268 36 L284 2 Q286 0 290 0 L484 0 L484 36 Z" fill="var(--navy)"/>
  </svg>
  <p class="company-tag">KAJU Freightways &amp; Energy</p>
</section>

</body>
</html>
```